Lunelle Rosa Hair Fancy Business Card’s

I want my business cards to be elite, original and very classy. I want the business cards to match the colors of my logo and to match the design posted. I would love the design of the picture I posted

I want the card all white .
The dripping on the top of the card I want it to match the pink color in my logo that’s also posted .
I need my logo on the business card !
I need my Instagram- @lunelle.rosa.hair__
And my phone number - 555 207 3962

Target Market(s)

My target market is young woman age 23 to older woman to the age of 65
I want both older and younger women to love my design . I don’t want any cheap looking business cards

Industry/Entity Type

Hair And Beauty

Contact Information for Business Card

Add my logo
Add my Instagram- @lunelle.rosa.hair__
My number - 555 207 3962
My website- www.lunellerosahair.example

Font styles to use
Serif
Script

Colors
ffffff
e667a6
e34298

Requirements
Must have
• The business cards must have my logo, my number , my website, and my Instagram!
Nice to have
• Nice to have glitter words that match my logo
• The business cards must look classy and mature
• I want them to be very unique!!
Should not have
• Should not have any colors that doesn’t match my logo ! This is very important! Please

```html
<!DOCTYPE html>
<html lang="en">
<head>
<meta charset="utf-8">
<title>Lunelle Rosa Hair – Business Card</title>
<link rel="stylesheet" href="https://fonts.googleapis.com/css2?family=Lato:wght@400;700&display=swap">
<style>
  :root {
    --canvas-bg: #e9e9eb;
    --card-dark: #1b1b1c;
    --card-light: #f4f4f5;
    --pink: #e34298;
    --pink-soft: #e667a6;
    --ink: #3a3a3c;
    --divider: #cfcfd2;
  }
  * { box-sizing: border-box; margin: 0; padding: 0; }
  html, body {
    width: 1200px;
    height: 1015px;
    overflow: hidden;
    background: var(--canvas-bg);
    font-family: "Lato", Arial, sans-serif;
  }
  .sheet {
    width: 1200px;
    height: 1015px;
    display: flex;
    flex-direction: column;
    align-items: center;
    justify-content: center;
    gap: 50px;
  }
  .card {
    position: relative;
    width: 740px;
    height: 423px;
    box-shadow: 0 10px 28px rgba(0,0,0,0.22);
    overflow: hidden;
  }
  .card::after {
    content: "";
    position: absolute;
    left: 0; right: 0; bottom: 0;
    height: 14px;
    background: var(--pink);
  }
  .card--front { background: var(--card-dark); }
  .card--back { background: var(--card-light); }

  .brand-name {
    font-family: "Lato", Arial, sans-serif;
    font-weight: 700;
    color: var(--pink);
    letter-spacing: 0.06em;
    text-transform: uppercase;
    white-space: nowrap;
  }
  .card--front .brand-name {
    position: absolute;
    left: 0; right: 0;
    top: 178px;
    text-align: center;
    font-size: 44px;
  }
  .card--back .brand-name {
    position: absolute;
    left: 40px;
    top: 196px;
    width: 330px;
    text-align: center;
    font-size: 30px;
  }
  .divider {
    position: absolute;
    left: 385px;
    top: 60px;
    width: 1px;
    height: 300px;
    background: var(--divider);
  }
  .contact-list {
    position: absolute;
    left: 420px;
    top: 92px;
    list-style: none;
  }
  .contact-list li {
    display: flex;
    align-items: center;
    gap: 12px;
    font-size: 19px;
    color: var(--ink);
    height: 32px;
  }
  .contact-list li.contact--social { margin-top: 26px; }
  .icon { width: 22px; height: 22px; flex: none; }
</style>
</head>
<body>
<main class="sheet">
  <section class="card card--front" aria-label="Card front">
    <p class="brand-name">Lunelle Rosa Hair</p>
  </section>

  <section class="card card--back" aria-label="Card back">
    <p class="brand-name">Lunelle Rosa Hair</p>
    <div class="divider"></div>
    <ul class="contact-list">
      <li class="contact--phone">
        <svg class="icon" viewBox="0 0 24 24" aria-hidden="true">
          <circle cx="12" cy="12" r="11" fill="none" stroke="#e34298" stroke-width="2"/>
          <path d="M8.2 6.5l2 .1.9 2.6-1.3 1.1a7 7 0 0 0 3.9 3.9l1.1-1.3 2.6.9.1 2c-.2.6-.8 1-1.5 1A9.5 9.5 0 0 1 7.2 8c0-.7.4-1.3 1-1.5z" fill="#e34298"/>
        </svg>
        <span>555 207 3962</span>
      </li>
      <li class="contact--web">
        <svg class="icon" viewBox="0 0 24 24" aria-hidden="true">
          <circle cx="12" cy="12" r="11" fill="#e34298"/>
          <g fill="none" stroke="#fff" stroke-width="1.3">
            <circle cx="12" cy="12" r="7"/>
            <ellipse cx="12" cy="12" rx="3" ry="7"/>
            <path d="M5 12h14M6.2 8.5h11.6M6.2 15.5h11.6"/>
          </g>
        </svg>
        <span>www.lunellerosahair.example</span>
      </li>
      <li class="contact--social">
        <svg class="icon" viewBox="0 0 24 24" aria-hidden="true">
          <circle cx="12" cy="12" r="10.5" fill="none" stroke="#e34298" stroke-width="1.6"/>
        </svg>
        <span>@lunelle.rosa.hair__</span>
      </li>
    </ul>
  </section>
</main>
</body>
</html>
```